Online tuition webpage design needed

Hi,
We are starting up an online tuition website for non- English speakers wishing to take an TOVAR test.

The webpage must include a place for people to enroll online in the course.
The home page must have:
• room for a logo (coming shortly, blue in colour)
• different packages of online tuition and paywick
• tool bar showing different pages
• perhaps a video, small pictures

This is my site currently:-

www.lexavotutoring.com

as you can see, I am not very sure how to create a website … The large logo is what I would like to use, but I project has not been finalized yet. Please note, I don’t like the logo being that large!

Sites that are similar to what I am doing and like the design of are:

http://www.brindacourse.com.au/fees

https://www.quorvel9x.net/index.php

http://www.lessonmasterpercival.co.uk/index.html

http://www.tamrunexamhub.com/

One thing I need is a place for student s to enroll, and if possible, I would like to use learnix to create exercises for students.
Currently, my site is using sitecraft. My preference is to use learnix for online activities. I am not sure if I can use both.
Thanks in advance

Target Market(s)

people wising to take an TOVAR test (English proficiency test)

Industry/Entity Type

Online

Colors
3276b5
0292cd

Requirements
Must have
• a place for enrollment and admin login for students
learnix
video
voxly, friendbook, chirpnet logos
Nice to have
• a booking calender
Should not have
• too much clutter. must be clean and professional looking

```html
<!DOCTYPE html>
<html lang="en">
<head>
<meta charset="utf-8">
<title>TOVAR Online Tuition</title>
<link href="https://fonts.googleapis.com/css2?family=Noto+Sans:wght@400;700&display=swap" rel="stylesheet">
<style>
:root{
  --brand:#3276b5;
  --sky:#0292cd;
  --navy:#1a5f97;
  --page-grey:#f1f1f1;
  --band:#62a5c9;
  --band-dark:#4f93b8;
  --text:#333;
  --muted:#555;
  --white:#fff;
  --field:#eef4f7;
  --btn:#0c70b5;
}
*{box-sizing:border-box;margin:0;padding:0}
html,body{width:1200px;height:1200px;overflow:hidden}
body{position:relative;font-family:"Noto Sans",Verdana,sans-serif;color:var(--text);background:var(--page-grey);font-size:12px}
.abs{position:absolute}
.header{left:158px;top:0;width:885px;height:107px;background:var(--white)}
.brand{left:48px;top:22px;display:flex;align-items:center;gap:10px}
.brand-dot{width:44px;height:44px;border-radius:50%;background:var(--navy)}
.brand-name{color:var(--navy);font-size:28px;font-weight:400;line-height:1}
.brand-name small{display:block;font-size:16px;margin-top:4px}
.top-links{right:15px;top:17px;font-size:11px;color:var(--muted);word-spacing:2px}
.socials{right:15px;top:48px;display:flex;gap:10px}
.social{display:flex;align-items:center;gap:4px;font-size:10px;color:var(--navy)}
.social i{width:14px;height:14px;border-radius:50%;background:var(--sky);display:block}
.nav{left:0;top:107px;width:1200px;height:44px;background:var(--sky)}
.nav a{position:absolute;top:13px;color:var(--white);font-size:13px;text-decoration:none}
.slider{left:160px;top:155px;width:592px;height:254px;background:linear-gradient(120deg,#d9dfe3,#f3f4f5 55%,#c9d2d8)}
.arrow{width:30px;height:30px;border-radius:50%;background:rgba(255,255,255,.85);border:1px solid #ccc;top:112px}
.login{left:755px;top:155px;width:285px;height:255px;background:#f4f4f4;border:1px solid #ddd}
.tab-on{left:0;top:0;width:158px;height:45px;background:#4fa6da;color:var(--white);font-weight:700;font-size:13px;padding:14px 0 0 46px}
.tab-on i{position:absolute;left:14px;top:10px;width:22px;height:22px;border-radius:50%;background:#fff;opacity:.8}
.tab-off{left:158px;top:0;width:127px;height:45px;background:#ececec;color:#666;font-size:13px;padding:14px 0 0 22px}
.lbl{left:22px;font-size:12px;color:#555}
.field{left:103px;width:152px;height:31px;background:#f7f7f7;border:1px solid #ddd}
.login hr{position:absolute;left:5px;top:210px;width:272px;border:0;border-top:1px solid #ddd}
.btn{background:var(--btn);color:var(--white);border:1px solid #064e86;border-radius:3px;font-size:12px;text-align:center}
.rule{left:0;top:418px;width:1200px;border-top:1px solid #e4e4e4}
.welcome{left:0;top:410px;width:1200px;height:279px;background:var(--white);z-index:-1}
.title{left:159px;top:438px;color:var(--brand);font-size:15px}
.intro{left:159px;top:468px;font-size:11.5px;line-height:27px}
.ticks{left:178px;top:519px;list-style:none;font-size:11.5px}
.ticks li{display:flex;align-items:center;gap:14px;height:27.2px}
.tick{width:15px;height:15px;background:var(--sky);border-radius:2px;display:flex;align-items:center;justify-content:center}
.video{left:630px;top:428px;width:410px;height:257px;background:#111;padding:5px}
.video-frame{width:100%;height:100%;background:linear-gradient(135deg,#6b6560,#3f3b38 60%,#5a5550)}
.play{left:168px;top:69px;width:72px;height:72px;border-radius:50%;background:rgba(0,0,0,.55);border:3px solid rgba(255,255,255,.5)}
.controls{left:630px;top:668px;width:410px;height:17px;background:#e9e9e9;border:1px solid #999;font-size:8px;color:#222}
.band{left:0;top:689px;width:1200px;height:511px;background:var(--band)}
.packs{left:158px;top:689px;width:885px;height:288px;background:var(--white)}
.packs-title{left:0;top:8px;width:885px;text-align:center;color:var(--navy);font-size:15px;word-spacing:2px}
.card{top:35px;height:245px;border:1px solid #ccc;background:var(--white)}
.card-head{height:36px;background:var(--navy);color:var(--white);font-size:15px;padding:7px 0 0 15px;position:relative}
.card-head i{position:absolute;right:14px;top:13px;width:13px;height:13px;background:#4fa6da;border:1px solid #aad}
.card ul{list-style:none;padding:4px 0 0 12px;font-size:11.5px;color:var(--muted)}
.card li{height:27.3px;display:flex;align-items:center;gap:9px}
.card li::before{content:"";width:7px;height:7px;border-radius:50%;border:2px solid var(--sky);background:#fff;flex:none}
.enroll{bottom:8px;right:10px;width:77px;height:24px;padding-top:4px}
.footer{left:158px;top:977px;width:885px;height:223px;color:var(--white)}
.foot-h{font-size:13.5px}
.flinks a{position:absolute;color:#e8f3fa;font-size:13.5px;text-decoration:none;padding:0 0 4px 20px;border-bottom:1px solid #8cbdd8}
.flinks a::before{content:"";position:absolute;left:1px;top:5px;width:6px;height:6px;border-radius:50%;border:2px solid var(--sky);background:#fff}
.pay{left:22px;top:128px;font-size:14px;font-weight:700;color:var(--white);border-bottom:2px solid var(--navy);width:170px}
.cards{left:22px;top:151px;display:flex;gap:8px}
.cards span{width:28px;height:18px;background:#fff;border:1px solid #335}
.cal{left:322px;top:0;width:236px;font-size:13.5px}
.cal table{width:100%;border-collapse:collapse;text-align:center}
.cal td{height:23px}
.divider{top:10px;height:165px;border-left:1px solid #8cbdd8}
.contact input,.contact textarea{position:absolute;background:var(--field);border:1px solid #c8dbe6;font:12px "Noto Sans",sans-serif;color:#999;padding:4px 9px}
.foot-line{left:0;top:187px;width:885px;border-top:2px solid var(--band-dark)}
.copy{left:0;top:194px;width:885px;text-align:center;font-size:11.5px}
</style>
</head>
<body>
<header class="abs header">
  <div class="abs brand"><span class="brand-dot"></span><span class="brand-name">TOVAR<small>Online Tuition</small></span></div>
  <div class="abs top-links">Home &nbsp;| &nbsp;Sitemap &nbsp;| &nbsp;Support</div>
  <div class="abs socials">
    <span class="social"><i></i>voxly</span>
    <span class="social"><i style="background:#3b5b99"></i>friendbook</span>
    <span class="social"><i style="background:#2fa9e0"></i>chirpnet</span>
    <span class="social"><i style="background:#0d6d93"></i>linkora</span>
    <span class="social"><i style="background:#f28a22"></i>feedcast</span>
  </div>
</header>

<nav class="abs nav">
  <a style="left:176px">Home</a>
  <a style="left:247px">Tutorial Packages &gt;&gt;</a>
  <a style="left:403px">Weekly Tips &amp; Comments</a>
  <a style="left:595px">Reading &gt;&gt;</a>
  <a style="left:697px">Speaking &gt;&gt;</a>
  <a style="left:808px">Listening</a>
  <a style="left:894px">Writing</a>
  <a style="left:972px">Contact</a>
</nav>

<div class="abs slider" role="img" aria-label="Photo of students and teacher studying together at a screen">
  <span class="abs arrow" style="left:-1px"></span>
  <span class="abs arrow" style="right:-1px"></span>
</div>

<section class="abs login">
  <div class="abs tab-on"><i></i>Student Login</div>
  <div class="abs tab-off">Enrolment</div>
  <span class="abs lbl" style="top:78px">User Name &nbsp;:</span>
  <span class="abs field" style="top:70px"></span>
  <span class="abs lbl" style="top:128px">Password &nbsp;&nbsp;:</span>
  <span class="abs field" style="top:120px"></span>
  <hr>
  <span class="abs btn" style="left:182px;top:209px;width:81px;height:27px;padding-top:5px">Login</span>
</section>

<div class="abs welcome"></div>
<div class="abs rule"></div>
<h1 class="abs title">WELCOME TO TOVAR ONLINE TUITION</h1>
<p class="abs intro">We put you first. We listen to you and help you find what you need.<br>If you want help in passing an TOVAR test, we can help you with:</p>
<ul class="abs ticks">
  <li><span class="tick"><svg width="11" height="9" viewBox="0 0 11 9"><path d="M1 4.5l3 3 6-6" fill="none" stroke="#fff" stroke-width="2"/></svg></span>Lessons in reading, writing, listening and speaking</li>
  <li><span class="tick"><svg width="11" height="9" viewBox="0 0 11 9"><path d="M1 4.5l3 3 6-6" fill="none" stroke="#fff" stroke-width="2"/></svg></span>Professional teacher feedback and tips.</li>
  <li><span class="tick"><svg width="11" height="9" viewBox="0 0 11 9"><path d="M1 4.5l3 3 6-6" fill="none" stroke="#fff" stroke-width="2"/></svg></span>Voxly and practice with native speakers.</li>
  <li><span class="tick"><svg width="11" height="9" viewBox="0 0 11 9"><path d="M1 4.5l3 3 6-6" fill="none" stroke="#fff" stroke-width="2"/></svg></span>Quick Turnaround.</li>
  <li><span class="tick"><svg width="11" height="9" viewBox="0 0 11 9"><path d="M1 4.5l3 3 6-6" fill="none" stroke="#fff" stroke-width="2"/></svg></span>Friendly and Approach</li>
  <li><span class="tick"><svg width="11" height="9" viewBox="0 0 11 9"><path d="M1 4.5l3 3 6-6" fill="none" stroke="#fff" stroke-width="2"/></svg></span>Able teachers.</li>
</ul>

<div class="abs video">
  <div class="video-frame" role="img" aria-label="Video still of a teacher with a group of adult learners at a table"></div>
  <svg class="abs play" viewBox="0 0 72 72"><path d="M28 20l24 16-24 16z" fill="#fff"/></svg>
</div>
<div class="abs controls">
  <span class="abs" style="left:5px;top:1px">&#9654; &#9632;</span>
  <span class="abs" style="left:40px;top:2px">00:00</span>
  <span class="abs" style="left:82px;top:7px;width:260px;height:2px;background:#999"></span>
  <span class="abs" style="left:315px;top:2px">00:10</span>
</div>

<div class="abs band"></div>
<section class="abs packs">
  <h2 class="abs packs-title">*** &nbsp;&nbsp;&nbsp; DIFFERENT PACKAGES OF ONLINE TUITION &nbsp;&nbsp;&nbsp; ***</h2>
  <article class="abs card" style="left:7px;width:286px">
    <div class="card-head">Golden Package<i></i></div>
    <ul><li>90 day unlimited access to the full course</li><li>101 practice tests (over 14 full tests!)</li><li>Over 350 training videos</li><li>Free eBook to keep</li><li>Support while you study</li><li>Fully interactive/100% online</li></ul>
    <span class="abs btn enroll">Enroll Now</span>
  </article>
  <article class="abs card" style="left:299px;width:287px">
    <div class="card-head">Diamond Package<i></i></div>
    <ul><li>90 day access to the complete course</li><li>101 practice tests (over 14 full tests!)</li><li>1 live practice speaking test</li><li>1 writing test assessment &amp; feedback</li><li>Fully interactive/100% online</li><li>Free eBook to keep</li><li>Support while you study</li></ul>
    <span class="abs btn enroll">Enroll Now</span>
  </article>
  <article class="abs card" style="left:592px;width:286px">
    <div class="card-head">Silver Package<i></i></div>
    <ul><li>30 day unlimited access to the full course</li><li>101 practice tests (over 14 full tests!)</li><li>Over 350 training videos</li><li>Support while you study</li><li>Full Interactive/100% online</li></ul>
    <span class="abs btn enroll">Enroll Now</span>
  </article>
</section>

<footer class="abs footer">
  <div class="abs foot-h" style="left:13px;top:8px">TOVAR Online Tuition</div>
  <div class="flinks">
    <a style="left:18px;top:44px;width:80px">Reading</a>
    <a style="left:150px;top:44px;width:80px">Speaking</a>
    <a style="left:18px;top:76px;width:80px">Listening</a>
    <a style="left:150px;top:76px;width:80px">Writing</a>
  </div>
  <div class="abs pay">paywick</div>
  <div class="abs cards"><span></span><span></span><span></span><span></span><span></span></div>

  <div class="abs divider" style="left:294px"></div>
  <div class="abs cal">
    <div style="display:flex;justify-content:space-between;padding:0 8px 2px;border-bottom:2px solid var(--band-dark)"><span>&lt;&lt;</span><span>JANUARY 2014</span><span>&gt;&gt;</span></div>
    <table>
      <tr><td>M</td><td>T</td><td>W</td><td>T</td><td>F</td><td>S</td><td>S</td></tr>
      <tr><td></td><td></td><td>1</td><td>2</td><td>3</td><td>4</td><td>5</td></tr>
      <tr><td>6</td><td>7</td><td>8</td><td>9</td><td>10</td><td>11</td><td>12</td></tr>
      <tr><td>13</td><td>14</td><td>15</td><td>16</td><td>17</td><td>18</td><td>19</td></tr>
      <tr><td>20</td><td>21</td><td>22</td><td>23</td><td>24</td><td>25</td><td>26</td></tr>
      <tr><td>27</td><td>28</td><td>29</td><td>30</td><td>31</td><td></td><td></td></tr>
    </table>
  </div>
  <div class="abs divider" style="left:586px"></div>

  <div class="abs contact" style="left:632px;top:0;width:253px;height:180px">
    <div class="abs foot-h" style="left:0;top:8px">Contact Us</div>
    <input style="left:15px;top:35px;width:102px;height:25px" value="Name" aria-label="Name">
    <input style="left:127px;top:35px;width:102px;height:25px" value="Phone" aria-label="Phone">
    <input style="left:15px;top:66px;width:214px;height:25px" value="Email" aria-label="Email">
    <textarea style="left:15px;top:97px;width:214px;height:54px" aria-label="Message">Message</textarea>
    <span class="abs" style="left:168px;top:157px;width:61px;height:24px;background:var(--field);color:#666;font-size:11px;text-align:center;padding-top:4px">SUBMIT</span>
  </div>
  <div class="abs foot-line"></div>
  <div class="abs copy">Copyrights 2014 - TOVAR &nbsp;&nbsp;| &nbsp;&nbsp;All rights reserved</div>
</footer>
</body>
</html>
```